Full re-design of visual identity

We have just re-designed our logo and would like to apply it on our folders, business cards, stationery, and etc... we are attaching new logo + the material we need to re-design... we will provide full corel draw files to help make job easier and also because lot of icons and artwork can be still used...

any doubts we are at your disposal. thanks in advance.

```html
<!DOCTYPE html>
<html lang="en">
<head>
<meta charset="utf-8">
<title>Corvalink – Folder and Letterhead</title>
<link href="https://fonts.googleapis.com/css2?family=Exo+2:wght@400;600;700&display=swap" rel="stylesheet">
<style>
:root{
  --bg:#ececec;
  --paper:#ffffff;
  --brand-grey:#7d7d7d;
  --text:#6a6a6a;
  --orange:#ef7d2c;
  --orange-deep:#d9622a;
  --rule:#8a8a8a;
}
*{box-sizing:border-box;margin:0;padding:0}
html,body{width:1200px;height:1000px;overflow:hidden}
body{background:var(--bg);font-family:"Exo 2",sans-serif;color:var(--text);position:relative}
.sheet{position:absolute;background:var(--paper);box-shadow:0 6px 22px rgba(0,0,0,.12);overflow:hidden}
.folder{left:70px;top:110px;width:500px;height:707px}
.letterhead{left:630px;top:110px;width:500px;height:707px}
.brand{display:flex;align-items:center;gap:10px}
.brand-name{font-weight:700;color:var(--brand-grey);letter-spacing:-1px;line-height:1}
.brand-dot{border-radius:50%;background:var(--orange)}
.folder .brand{position:absolute;left:120px;top:200px}
.folder .brand-name{font-size:62px}
.folder .brand-dot{width:30px;height:30px}
.contact{list-style:none;font-size:9px;line-height:1.55}
.contact li{display:flex;align-items:flex-start;gap:6px}
.contact svg{width:8px;height:8px;margin-top:3px;flex:none;fill:var(--orange)}
.folder .contact{position:absolute;left:40px;top:470px}
.folder-swoosh{position:absolute;left:0;bottom:0;width:500px;height:150px}
.letterhead .brand{position:absolute;right:40px;top:48px}
.letterhead .brand-name{font-size:34px}
.letterhead .brand-dot{width:16px;height:16px}
.fields{position:absolute;left:40px;top:108px;display:flex;gap:36px;font-size:8px}
.field-label{display:block;color:var(--orange);font-weight:700;font-size:8.5px;text-transform:uppercase}
.fields-rule{position:absolute;left:40px;top:128px;width:230px;border-top:1px solid var(--rule)}
.letter-title{position:absolute;left:100px;right:40px;top:172px;text-align:right;color:var(--orange);font-size:14px;font-weight:700}
.title-rule{position:absolute;left:100px;right:40px;top:196px;border-top:1px solid var(--rule)}
.letter-body{position:absolute;left:100px;right:40px;top:210px;font-size:8.5px;line-height:1.6;text-align:justify}
.letter-body p{margin-bottom:10px}
.body-rule{position:absolute;left:60px;right:40px;top:400px;border-top:1px solid var(--rule)}
.signature{position:absolute;right:60px;top:480px;font-size:18px;color:#333}
.signature-rule{position:absolute;left:280px;right:40px;top:512px;border-top:1px solid var(--rule)}
.letterhead .contact{position:absolute;left:330px;top:540px}
.letter-band{position:absolute;left:0;right:0;bottom:0;height:12px;background:var(--orange)}
</style>
</head>
<body>

<section class="sheet folder" aria-label="Presentation folder cover">
  <div class="brand"><span class="brand-name">corvalink</span><span class="brand-dot"></span></div>
  <ul class="contact">
    <li><svg viewBox="0 0 10 10"><path d="M5 0a3.5 3.5 0 0 0-3.5 3.5C1.5 6 5 10 5 10s3.5-4 3.5-6.5A3.5 3.5 0 0 0 5 0z"/></svg>48 Harbour Road, Westfield,<br>20410, Portugal</li>
    <li><svg viewBox="0 0 10 10"><path d="M2 0l2 2.5-1 1.2a6 6 0 0 0 3.3 3.3l1.2-1L10 8l-1.5 2C4 10 0 6 0 1.5z"/></svg>555-0147-22</li>
    <li><svg viewBox="0 0 10 10"><path d="M0 2h10v6H0zM0 2l5 3.5L10 2"/></svg>hello@corvalink.net</li>
    <li><svg viewBox="0 0 10 10"><circle cx="5" cy="5" r="5"/></svg>www.corvalink.net</li>
  </ul>
  <svg class="folder-swoosh" viewBox="0 0 500 150" preserveAspectRatio="none">
    <defs><linearGradient id="swoosh" x1="0" x2="1"><stop offset="0" stop-color="#d9622a"/><stop offset="1" stop-color="#f08a35"/></linearGradient></defs>
    <path d="M0 20 C140 100 320 110 500 80 L500 150 L0 150 Z" fill="url(#swoosh)"/>
  </svg>
</section>

<section class="sheet letterhead" aria-label="Letterhead">
  <div class="brand"><span class="brand-name">corvalink</span><span class="brand-dot"></span></div>
  <div class="fields">
    <div><span class="field-label">Subject</span>Lorem ipsum</div>
    <div><span class="field-label">Date</span>01/01/2014</div>
    <div><span class="field-label">Adressed to</span>Ana Moreno</div>
  </div>
  <div class="fields-rule"></div>
  <h1 class="letter-title">Lorem ipsum dolor sit ametconsectetur:</h1>
  <div class="title-rule"></div>
  <div class="letter-body">
    <p>Lorem ipsum dolor sit amet, consectetur adipiscing elit. Nulla sodales nisi vitae lorem ipsum dolor sit amet, consectetur adipiscing elit. Suspendisse feugiat eros nisl, a facilisis risus eleifend sed. Aliquam mauris enim, fermentum eu lacinia sit amet, laoreet eu felis. Nullam eleifend nulla in libero tristique.</p>
    <p>Ut vitae interdum diam, in euismod ante. Pellentesque volutpat, risus sit amet sodales hendrerit, mi turpis vulputate dolor, eget cursus nulla eros nec tellus. Nulla tincidunt molestie libero vel pretium. Donec condimentum nulla sit amet risus semper imperdiet. Duis congue eros nec diam blandit ac pellentesque sapien auctor.</p>
    <p>Best regards,</p>
  </div>
  <div class="body-rule"></div>
  <p class="signature">Paul Rivers</p>
  <div class="signature-rule"></div>
  <ul class="contact">
    <li><svg viewBox="0 0 10 10"><path d="M5 0a3.5 3.5 0 0 0-3.5 3.5C1.5 6 5 10 5 10s3.5-4 3.5-6.5A3.5 3.5 0 0 0 5 0z"/></svg>48 Harbour Road, Westfield,<br>20410, Portugal</li>
    <li><svg viewBox="0 0 10 10"><path d="M2 0l2 2.5-1 1.2a6 6 0 0 0 3.3 3.3l1.2-1L10 8l-1.5 2C4 10 0 6 0 1.5z"/></svg>555-0147-22</li>
    <li><svg viewBox="0 0 10 10"><path d="M0 2h10v6H0zM0 2l5 3.5L10 2"/></svg>hello@corvalink.net</li>
    <li><svg viewBox="0 0 10 10"><circle cx="5" cy="5" r="5"/></svg>www.corvalink.net</li>
  </ul>
  <div class="letter-band"></div>
</section>

</body>
</html>
```